BRELWINCare.co.uk - Mental Health Clinic for Child and Adolescents

Updated 29/01/2018***
I am not sure you guys are getting the idea regards to the opening page / homescreen layout. Can you look at the new images I have uploaded (page 5, 6 and 7) These are some of the layouts I like but to incorporate my chosen images, with the BRELWIN commissioner, buttons and a sliding header bar.
I have written a strong brief, I am looking for a website, preferably wordpress as i know they are easy to maintain. I am looking for a one page site, with the top / opening page being full screen image with drop down categories. I have made a rough design, see full brief in word doc attached, there is some freedom to play around with the design aspect but it will need to relay all the content provided. I like a minimal feel. I have also attached some images that may be useful, but will need a new logo for BRELWIN Care. I have attached some logo idea's, it is up to you decide whether you want to use them.
I would prefer the homepage as full screen image, and the categories offered as a drop down or over the main image.
I have also attached linked to some competitors websites:
https://www.vorimant-health.co.uk/
http://www.qlbn.org.uk/
Industry/Entity Type
Clinic
Number of Pages Required
1 page
Font styles to use
Look and feel
Each slider illustrates characteristics of the customer's brand and the style your logo design should communicate.

```html
<!DOCTYPE html>
<html lang="en">
<head>
<meta charset="utf-8">
<title>BRELWIN Care</title>
<link href="https://fonts.googleapis.com/css2?family=Lato:wght@400;700;900&display=swap" rel="stylesheet">
<style>
:root{
  --pink:#e6007e;
  --teal:#19b5c9;
  --teal-band:rgba(22,182,204,.88);
  --ink:#4a4a4a;
  --grey-text:#8a8a8a;
  --purple-a:#8e3f96;
  --purple-b:#5d1d66;
  --green-a:#b5d54a;
  --green-b:#8ab82a;
  --blue-a:#23458f;
  --blue-b:#00b2cf;
  --yellow:#e8e31a;
  --footer:#6b2473;
  --white:#fff;
}
*{box-sizing:border-box;margin:0;padding:0}
html,body{width:1200px;height:2765px;overflow:hidden;background:var(--white)}
body{font-family:'Lato',sans-serif;color:var(--ink);position:relative}
.abs{position:absolute}

/* header */
.site-header{position:absolute;left:0;top:0;width:1200px;height:114px;background:var(--white);border-bottom:2px solid #e4e4e4}
.brand{position:absolute;left:116px;top:34px;display:flex;align-items:center;gap:12px}
.brand-dot{width:40px;height:40px;border-radius:50%;background:var(--teal)}
.brand-name{font-weight:900;font-size:30px;color:var(--teal);letter-spacing:.5px}
.main-nav{position:absolute;left:366px;top:43px;display:flex;gap:20px;font-weight:700;font-size:14.5px;color:#222;text-transform:uppercase}
.main-nav .active{color:var(--teal)}

/* hero */
.hero{position:absolute;left:0;top:114px;width:1200px;height:570px;background:linear-gradient(100deg,#d9c6b6 0%,#efe6dc 35%,#b98a6e 60%,#e9e2d8 100%)}
.hero-band{position:absolute;left:0;top:494px;width:1200px;height:76px;background:var(--teal-band)}
.hero-caption{position:absolute;left:123px;top:22px;color:var(--white);font-size:22px;font-weight:700}
.hero-arrows{position:absolute;left:1016px;top:20px}

/* welcome */
.welcome{position:absolute;left:160px;top:750px;width:885px;height:273px;border:2px solid var(--pink);border-radius:72px;text-align:center}
.welcome-mark{position:absolute;left:420px;top:-26px;width:46px;height:46px;border-radius:50%;background:var(--yellow);box-shadow:0 0 0 10px var(--white)}
.welcome h1{margin-top:48px;font-size:32px;font-weight:700;color:#555}
.welcome h1 span{color:var(--teal)}
.welcome p{margin:18px auto 0;width:760px;font-size:17.5px;line-height:31px;color:var(--grey-text)}
.btn-pink{position:absolute;left:356px;top:244px;width:170px;height:46px;border-radius:23px;background:var(--pink);color:var(--white);font-weight:700;font-size:16px;line-height:46px;text-transform:uppercase;box-shadow:0 0 0 10px var(--white)}

/* audience panels */
.audience{position:absolute;top:1098px;height:356px;width:614px;text-align:center;color:var(--white)}
.audience.parents{left:0;background:linear-gradient(135deg,var(--purple-a),var(--purple-b))}
.audience.commissioners{left:614px;width:586px;background:linear-gradient(135deg,var(--green-a),var(--green-b))}
.audience svg{margin-top:42px}
.audience h2{margin-top:14px;font-size:24px;font-weight:700;text-transform:uppercase}
.audience p{margin:8px auto 0;width:400px;font-size:14.5px;line-height:19px}
.btn-outline{display:inline-block;border:2px solid var(--white);border-radius:24px;color:var(--white);font-weight:700;font-size:14.5px;text-transform:uppercase;text-align:center;background:transparent}
.audience .btn-outline{margin-top:24px;width:153px;height:45px;line-height:41px}

/* blogs */
.blogs{position:absolute;left:0;top:1454px;width:1200px;height:505px;background:linear-gradient(120deg,var(--blue-a),#1b72b4 50%,var(--blue-b));color:var(--white);text-align:center}
.blogs h2{margin-top:46px;font-size:30px;font-weight:700;text-transform:uppercase}
.blog-card{position:absolute;top:100px;width:300px;text-align:center}
.blog-photo{width:200px;height:200px;margin:0 auto;border-radius:50%;border:4px solid var(--yellow);background:radial-gradient(circle,#cfd6dc 0%,#9aa6b0 100%)}
.blog-card h3{margin-top:20px;font-size:20px;font-weight:700}
.blog-card p{margin:4px auto 0;width:240px;font-size:14px;line-height:18px}
.blog-card .btn-outline{margin-top:14px;width:153px;height:45px;line-height:41px}
.carousel-arrow{position:absolute;top:258px}

/* contact */
.contact{position:absolute;left:0;top:1959px;width:1200px;height:608px;background:linear-gradient(180deg,#f4f4f4,#e6e6e6)}
.contact-frame{position:absolute;left:273px;top:74px;width:658px;height:360px;border:2px solid var(--pink);border-bottom:none;border-radius:40px 40px 0 0}
.contact h2{position:absolute;left:0;width:1200px;top:52px;text-align:center;font-size:32px;font-weight:700;color:var(--pink);text-transform:uppercase}
.contact h2 span{background:#f2f2f2;padding:0 12px}
.contact-lines{position:absolute;left:0;top:116px;width:1200px;text-align:center;font-size:16.5px;line-height:31px;color:#333}
.feedback{position:absolute;left:350px;top:253px;width:531px;height:48px;border-radius:24px;background:var(--white);box-shadow:0 1px 4px rgba(0,0,0,.15)}
.feedback span{position:absolute;left:22px;top:14px;font-size:15px;color:#777}
.feedback b{position:absolute;right:4px;top:6px;width:126px;height:36px;border-radius:18px;background:var(--teal);color:var(--white);font-size:15px;line-height:36px;text-align:center;text-transform:uppercase}
.group-photo{position:absolute;left:138px;top:317px;width:894px;height:291px;background:linear-gradient(90deg,#c9b59a,#e3c8a5 30%,#8c4a3c 55%,#d8b08a 75%,#b9c4cc);border-radius:30px 30px 0 0}

/* footer */
.site-footer{position:absolute;left:0;top:2567px;width:1200px;height:198px;background:var(--footer);color:var(--white);text-align:center}
.footer-nav{margin-top:41px;display:flex;justify-content:center;gap:18px;font-weight:700;font-size:16px;text-transform:uppercase}
.copyright{margin-top:12px;font-size:15px}
.social{margin-top:22px;display:flex;justify-content:center;gap:10px}
.social span{width:40px;height:40px;border:2px solid var(--white);border-radius:50%}
</style>
</head>
<body>

<header class="site-header">
  <div class="brand"><span class="brand-dot"></span><span class="brand-name">BRELWIN</span></div>
  <nav class="main-nav">
    <span class="active">About Us</span><span>Our Team</span><span>Our Services</span><span>Blogs</span><span>Forum</span><span>Contact Us</span><span>Parents</span><span>Commisioners</span>
  </nav>
</header>

<section class="hero" role="img" aria-label="Photo of a girl talking with a smiling counsellor in a bright room">
  <div class="hero-band">
    <div class="hero-caption">ADHD and Austim Screening with 24 Hours</div>
    <svg class="hero-arrows" width="64" height="36" viewBox="0 0 64 36" fill="none" stroke="#fff" stroke-width="4" stroke-linecap="round" stroke-linejoin="round">
      <polyline points="18,6 6,18 18,30"/><polyline points="46,6 58,18 46,30"/>
    </svg>
  </div>
</section>

<section class="welcome">
  <span class="welcome-mark"></span>
  <h1>WELCOME TO <span>BRELWIN</span></h1>
  <p>Vivamus porttitor purus nisi eleifend libero a tempus libero lectus feugiat felis Morbi diam mauris viverra in gravida eu mattis in ante Morbi eget arcu Morbi porta libero id ullamcorper nonummy nibh ligula pulvinar metus eget consectetuer augue nisi quis lacus Ut</p>
  <span class="btn-pink">Read More</span>
</section>

<section class="audience parents">
  <svg width="60" height="62" viewBox="0 0 60 62" fill="#fff">
    <circle cx="18" cy="14" r="11"/><circle cx="42" cy="14" r="11"/>
    <path d="M2 58c0-16 7-28 16-28s16 12 16 28z"/><path d="M26 58c0-16 7-28 16-28s16 12 16 28z"/>
  </svg>
  <h2>Parents</h2>
  <p>Vivamus porttitor purus nisi eleifend libero a tempus libero lectus feugiat felis Morbi diam mauris viverra in gravida eu mattis in ante Morbi eget arcu Morbi porta libero id ullamcorper nonummy nibh ligula pulvina</p>
  <span class="btn-outline">Read More</span>
</section>

<section class="audience commissioners">
  <svg width="56" height="62" viewBox="0 0 56 62" fill="#fff">
    <circle cx="28" cy="18" r="14"/><path d="M4 62c0-16 10-26 24-26s24 10 24 26z"/>
  </svg>
  <h2>Commisioners</h2>
  <p>Vivamus porttitor purus nisi eleifend libero a tempus libero lectus feugiat felis Morbi diam mauris viverra in gravida eu mattis in ante Morbi eget arcu Morbi porta libero id ullamcorper nonummy nibh ligula pulvina</p>
  <span class="btn-outline">Read More</span>
</section>

<section class="blogs">
  <h2>Our Blogs</h2>
  <svg class="carousel-arrow" style="left:120px" width="26" height="40" viewBox="0 0 26 40" fill="none" stroke="#fff" stroke-width="4" stroke-linecap="round" stroke-linejoin="round"><polyline points="20,6 6,20 20,34"/></svg>
  <svg class="carousel-arrow" style="left:1070px" width="26" height="40" viewBox="0 0 26 40" fill="none" stroke="#fff" stroke-width="4" stroke-linecap="round" stroke-linejoin="round"><polyline points="6,6 20,20 6,34"/></svg>

  <article class="blog-card" style="left:141px;top:100px">
    <div class="blog-photo" role="img" aria-label="Photo of a girl in a striped top during a session"></div>
    <h3>Aorta libero ullamcorper</h3>
    <p>nonummy nibh ligula pulvinar metus eget consectetuer augue nisi quis</p>
    <span class="btn-outline">Read More</span>
  </article>
  <article class="blog-card" style="left:456px;top:108px">
    <div class="blog-photo" role="img" aria-label="Photo of a smiling woman seated at a table"></div>
    <h3>Fusce ultricies orci</h3>
    <p>nonummy nibh ligula pulvinar metus eget consectetuer augue nisi quis</p>
    <span class="btn-outline">Read More</span>
  </article>
  <article class="blog-card" style="left:768px;top:108px">
    <div class="blog-photo" role="img" aria-label="Photo of a boy sitting on a sofa"></div>
    <h3>Nulla rhoncus dictu</h3>
    <p>nonummy nibh ligula pulvinar metus eget consectetuer augue nisi quis</p>
    <span class="btn-outline">Read More</span>
  </article>
</section>

<section class="contact" role="region" aria-label="Contact">
  <div class="contact-frame"></div>
  <h2><span>Contact Us</span></h2>
  <div class="contact-lines">
    Phone Number: 0203 555 0192<br>
    Address:&nbsp; Ashgrove Suite 2B, 41-47 Mill Lane, London, E19 4PL<br>
    Opening Times: 9am – 5pm Mon-Fri<br>
    Email: enquiry@brelwincare.co.uk
  </div>
  <div class="feedback"><span>Type Feedback</span><b>Submit</b></div>
  <div class="group-photo" role="img" aria-label="Photo of five smiling teenagers sitting together on a sofa"></div>
</section>

<footer class="site-footer">
  <nav class="footer-nav"><span>About Us</span><span>Our Team</span><span>Our Services</span><span>Blogs</span><span>Contact Us</span><span>Parents</span><span>Commisioners</span></nav>
  <p class="copyright">© 2018 Company Name&nbsp; All right reserved</p>
  <div class="social"><span></span><span></span><span></span><span></span></div>
</footer>

</body>
</html>
```